Business Card Design for Training Business

Clear Path Coaching is a new business that delivers training and other services with a focus on topics related to mental health and wellbeing, for example, Wellmind Response Course, Resilience etc. We have a strong focus on evidence-based psychology and neuroscience. I have a logo which I will upload with the brief, so please consider colours that work well with the logo.
Target Market(s)
Adults, workplaces (particularly government and not-for-profits)
Industry/Entity Type
Business
Contact Information for Business Card
Head Strong TrainingSamantha SellwoodDirector0438 770 850sam@headstrongtraining.com.auwww.headstrongtraining.com.au

```html
<!DOCTYPE html>
<html lang="en">
<head>
<meta charset="utf-8">
<title>Clear Path Coaching – Business Card</title>
<link rel="stylesheet" href="https://fonts.googleapis.com/css2?family=Josefin+Sans:wght@300&family=Open+Sans:wght@400&family=Playfair+Display:ital,wght@1,500&display=swap">
<style>
  :root {
    --backdrop: #e9e6e1;
    --card: #ffffff;
    --teal: #2b9496;
    --teal-light: #4fb3b3;
    --ink: #2f2f2f;
    --ink-soft: #1a1a1a;
  }
  * { box-sizing: border-box; margin: 0; padding: 0; }
  html, body { width: 1200px; height: 892px; overflow: hidden; }
  body {
    background: var(--backdrop);
    font-family: "Open Sans", Arial, sans-serif;
    position: relative;
  }
  .card {
    position: absolute;
    left: 250px;
    width: 700px;
    height: 400px;
    background: var(--card);
    box-shadow: 0 4px 14px rgba(0,0,0,.12);
    overflow: hidden;
  }
  .card--front { top: 30px; }
  .card--back { top: 462px; }

  .brand-name {
    font-family: "Josefin Sans", Arial, sans-serif;
    font-weight: 300;
    color: var(--ink);
    text-transform: uppercase;
    white-space: nowrap;
    line-height: 1;
  }
  .brand-name__main { display: block; font-size: 40px; letter-spacing: .14em; }
  .brand-name__sub { display: block; font-size: 19px; letter-spacing: .38em; margin-top: 6px; }

  .card--front .brand-name {
    position: absolute;
    left: 56px; top: 44px;
  }
  .card--front .brand-name__sub { padding-left: 92px; }

  .person { position: absolute; left: 56px; top: 140px; }
  .person__name {
    font-family: "Playfair Display", Georgia, serif;
    font-style: italic;
    font-weight: 500;
    font-size: 32px;
    color: var(--teal);
    line-height: 1.1;
  }
  .person__role { font-size: 15px; color: var(--ink-soft); margin-top: 2px; }

  .contact { position: absolute; left: 56px; top: 240px; list-style: none; }
  .contact__item {
    display: flex; align-items: center; gap: 18px;
    font-size: 18px; color: var(--ink-soft);
    height: 30px;
  }
  .contact__icon { width: 18px; height: 18px; flex: none; }

  .band { position: absolute; left: 0; top: 0; width: 700px; height: 400px; }

  .card--back .lockup {
    position: absolute; inset: 0;
    display: flex; flex-direction: column; align-items: center; justify-content: center;
    gap: 24px;
  }
  .lockup__dot {
    width: 96px; height: 96px; border-radius: 50%;
    background: radial-gradient(circle, #eef8f7 0%, var(--teal-light) 100%);
  }
  .card--back .brand-name { text-align: center; }
</style>
</head>
<body>

<section class="card card--front" aria-label="Business card front">
  <svg class="band" viewBox="0 0 700 400" aria-hidden="true">
    <polygon points="520,0 640,0 610,400 480,400" fill="var(--teal)"/>
    <circle cx="565" cy="235" r="112" fill="var(--teal)"/>
    <circle cx="565" cy="235" r="100" fill="var(--card)"/>
  </svg>

  <div class="brand-name">
    <span class="brand-name__main">Clear Path</span>
    <span class="brand-name__sub">Coaching</span>
  </div>

  <div class="person">
    <p class="person__name">Rebecca Tanfield</p>
    <p class="person__role">Director</p>
  </div>

  <ul class="contact">
    <li class="contact__item">
      <svg class="contact__icon" viewBox="0 0 18 18" aria-hidden="true">
        <rect width="18" height="18" fill="var(--ink-soft)"/>
        <path d="M5 4h2.5l1 3-1.5 1a7 7 0 0 0 3 3l1-1.5 3 1V13a1 1 0 0 1-1 1A9 9 0 0 1 4 5a1 1 0 0 1 1-1z" fill="#fff"/>
      </svg>
      <span>0491 362 517</span>
    </li>
    <li class="contact__item">
      <svg class="contact__icon" viewBox="0 0 18 18" aria-hidden="true">
        <rect width="18" height="18" fill="var(--ink-soft)"/>
        <rect x="3.5" y="5" width="11" height="8" fill="none" stroke="#fff" stroke-width="1.3"/>
        <path d="M3.5 5l5.5 4.5L14.5 5" fill="none" stroke="#fff" stroke-width="1.3"/>
      </svg>
      <span>bec@clearpathcoaching.example.au</span>
    </li>
    <li class="contact__item">
      <svg class="contact__icon" viewBox="0 0 18 18" aria-hidden="true">
        <rect width="18" height="18" fill="var(--ink-soft)"/>
        <circle cx="9" cy="9" r="5.5" fill="none" stroke="#fff" stroke-width="1.2"/>
        <ellipse cx="9" cy="9" rx="2.4" ry="5.5" fill="none" stroke="#fff" stroke-width="1"/>
        <path d="M3.5 9h11" stroke="#fff" stroke-width="1"/>
      </svg>
      <span>www.clearpathcoaching.example.au</span>
    </li>
  </ul>
</section>

<section class="card card--back" aria-label="Business card back">
  <div class="lockup">
    <div class="lockup__dot" aria-hidden="true"></div>
    <div class="brand-name">
      <span class="brand-name__main">Clear Path</span>
      <span class="brand-name__sub">Coaching</span>
    </div>
  </div>
</section>

</body>
</html>
```